Black card, Logo on front, in brushed silver, embossed or stamped
details centred on the back of the card written in Serif Old type face
Hotel
Red Heron Hotel Motel (or smaller logo)
your hosts
Brendan and Corina Walsh
left bottom:
7 Halvorn Street
Merrowdale NSW 2634
right bottom:
P: 02 61738495
M: 0438 512 764
W: www.redheronhotel.com.au
E: redheronhotel@mailvista.com
facebook emblem: @RedHeronHotel
instagram emblem: @redheronhotel

```html
<!DOCTYPE html>
<html lang="en">
<head>
<meta charset="utf-8">
<title>Red Heron Hotel – Business Card</title>
<link href="https://fonts.googleapis.com/css2?family=EB+Garamond:wght@400;500&display=swap" rel="stylesheet">
<style>
  :root {
    --backdrop: #2b2b2b;
    --card: #060606;
    --silver: #c4c4c4;
    --silver-dim: #8a8a8a;
    --text: #ededed;
    --rule: #9a9a9a;
  }
  html, body {
    margin: 0;
    width: 1200px;
    height: 900px;
    overflow: hidden;
    background: var(--backdrop);
    font-family: "EB Garamond", Georgia, serif;
  }
  .canvas {
    position: relative;
    width: 1200px;
    height: 900px;
  }
  .card {
    position: absolute;
    width: 620px;
    height: 354px;
    background: var(--card);
    box-shadow: 0 14px 30px rgba(0,0,0,0.55);
    overflow: hidden;
  }
  .card-front { left: 150px; top: 70px; }
  .card-back { left: 430px; top: 476px; }

  .brand {
    display: flex;
    align-items: center;
    gap: 14px;
    color: var(--silver);
    font-weight: 500;
    letter-spacing: 0.06em;
    text-transform: uppercase;
    white-space: nowrap;
  }
  .brand-dot {
    border-radius: 50%;
    background: var(--silver-dim);
  }
  .card-front .brand {
    position: absolute;
    left: 0; right: 0; top: 150px;
    justify-content: center;
    font-size: 34px;
  }
  .card-front .brand-dot { width: 40px; height: 40px; }

  .card-back .brand {
    position: absolute;
    left: 0; right: 0; top: 92px;
    justify-content: center;
    font-size: 22px;
  }
  .card-back .brand-dot { width: 22px; height: 22px; }

  .hosts {
    position: absolute;
    right: 340px;
    top: 150px;
    text-align: right;
    color: var(--text);
  }
  .host-names { font-size: 21px; font-weight: 500; margin: 0; }
  .host-role { font-size: 14px; color: var(--silver-dim); margin: 0 0 12px; }
  .address { font-size: 16px; line-height: 1.25; margin: 0; font-style: normal; }

  .divider {
    position: absolute;
    left: 296px;
    top: 150px;
    width: 1px;
    height: 78px;
    background: var(--rule);
  }

  .contacts {
    position: absolute;
    left: 312px;
    top: 144px;
    margin: 0;
    padding: 0;
    list-style: none;
    color: var(--text);
    font-size: 15px;
    line-height: 21px;
  }
  .contacts li { display: flex; align-items: center; gap: 8px; white-space: nowrap; }
  .contacts svg { width: 11px; height: 11px; fill: none; stroke: var(--silver); stroke-width: 1.4; }
  .web-rule {
    position: absolute;
    left: 510px; right: 0;
    top: 218px;
    height: 1px;
    background: var(--rule);
  }

  .socials {
    position: absolute;
    left: 0; right: 0;
    bottom: 34px;
    display: flex;
    align-items: center;
    gap: 12px;
    color: var(--text);
    font-size: 16px;
  }
  .socials .rule { height: 1px; background: var(--rule); }
  .socials .rule-left { width: 150px; }
  .socials .rule-right { flex: 1; }
  .social { display: flex; align-items: center; gap: 6px; white-space: nowrap; }
  .social-mark { width: 11px; height: 11px; background: var(--silver-dim); }
</style>
</head>
<body>
<main class="canvas">

  <section class="card card-front" aria-label="Card front">
    <div class="brand"><span class="brand-dot"></span>Red Heron Hotel</div>
  </section>

  <section class="card card-back" aria-label="Card back">
    <div class="brand"><span class="brand-dot"></span>Red Heron Hotel</div>

    <div class="hosts">
      <p class="host-names">Brendan and Corina Walsh</p>
      <p class="host-role">Your Hosts</p>
      <address class="address">7 Halvorn Street<br>Merrowdale NSW 2634</address>
    </div>

    <div class="divider"></div>

    <ul class="contacts">
      <li><svg viewBox="0 0 12 12"><path d="M2 1.5l2 0 1 2.5-1.3 1a6 6 0 0 0 3.3 3.3l1-1.3 2.5 1v2a1 1 0 0 1-1 1A9 9 0 0 1 1 2.5a1 1 0 0 1 1-1z"/></svg>02 61738495</li>
      <li><svg viewBox="0 0 12 12"><rect x="3" y="1" width="6" height="10" rx="1"/><path d="M5.5 9h1"/></svg>0438 512 764</li>
      <li><svg viewBox="0 0 12 12"><circle cx="6" cy="6" r="2"/><path d="M8 6v1a1.5 1.5 0 0 0 3 0V6a5 5 0 1 0-2 4"/></svg>redheronhotel@mailvista.com</li>
      <li><svg viewBox="0 0 12 12"><circle cx="6" cy="6" r="5"/><ellipse cx="6" cy="6" rx="2.2" ry="5"/><path d="M1 6h10"/></svg>www.redheronhotel.com.au</li>
    </ul>
    <div class="web-rule"></div>

    <div class="socials">
      <span class="rule rule-left"></span>
      <span class="social"><span class="social-mark"></span>@RedHeronHotel</span>
      <span class="social"><span class="social-mark"></span>@redheronhotel</span>
      <span class="rule rule-right"></span>
    </div>
  </section>

</main>
</body>
</html>
```